The most modern business card ever !!!

Our company call “Vendalo”. Vendalo is a technology company specialized in cruises solutions. Out main product is a platform to reserve cruises. This is a revolutionary platform that make easier to travel agencies and final users to reserve cruises across dozen companies like tibba, wernu, hpv, dgb, etc..We are a “start up”, with a young team of developers and we want to transmit it.. For it, we want something different, a modern business card that represent cruises and technology.. When someone receive this card, this person should say: wowww this is different… this is modern… this is a cruise related company..
- diferent, modern
- traditions business card

```html
<!DOCTYPE html>
<html lang="en">
<head>
<meta charset="utf-8">
<title>Vendalo Business Card</title>
<link href="https://fonts.googleapis.com/css2?family=Lato:wght@400;700&display=swap" rel="stylesheet">
<style>
  :root {
    --backdrop: #2b2b2b;
    --card-dark: #2a2a2a;
    --card-light: #f4f6f5;
    --ink: #151515;
    --ink-soft: #333333;
    --accent: #2aa7df;
    --wordmark-dark: #1e1e1e;
  }
  html, body {
    margin: 0;
    width: 1200px;
    height: 1200px;
    overflow: hidden;
    background: var(--backdrop);
    font-family: "Lato", sans-serif;
  }
  .stage {
    position: relative;
    width: 1200px;
    height: 1200px;
  }
  .card {
    position: absolute;
    top: 212px;
    width: 402px;
    height: 706px;
    border-radius: 24px;
    box-sizing: border-box;
  }
  .card--back {
    left: 182px;
    background: var(--card-dark);
    display: flex;
    align-items: center;
    justify-content: center;
  }
  .card--front {
    left: 617px;
    background: var(--card-light);
    text-align: center;
  }
  .wordmark {
    margin: 0;
    font-weight: 400;
    font-size: 68px;
    letter-spacing: 2px;
    line-height: 1;
  }
  .card--back .wordmark {
    color: var(--wordmark-dark);
    margin-top: -6px;
  }
  .card--front .wordmark {
    color: var(--ink);
    position: absolute;
    top: 100px;
    left: 0;
    right: 0;
  }
  .holder {
    position: absolute;
    top: 412px;
    left: 0;
    right: 0;
  }
  .holder__name {
    margin: 0;
    font-weight: 700;
    font-size: 33px;
    color: var(--ink);
    line-height: 1.1;
  }
  .holder__role {
    margin: 6px 0 0;
    font-weight: 400;
    font-size: 23px;
    color: var(--accent);
  }
  .contact {
    position: absolute;
    top: 524px;
    left: 0;
    right: 0;
    font-size: 22px;
    color: var(--ink-soft);
    line-height: 31px;
  }
  .contact p { margin: 0; }
  .contact .highlight { color: var(--accent); }
</style>
</head>
<body>
<main class="stage">
  <section class="card card--back">
    <p class="wordmark">Vendalo</p>
  </section>
  <section class="card card--front">
    <p class="wordmark">Vendalo</p>
    <div class="holder">
      <h1 class="holder__name">Dara Lenko</h1>
      <p class="holder__role">Director</p>
    </div>
    <div class="contact">
      <p>+351 420 715</p>
      <p>info@vendalo.com</p>
      <p>www.<span class="highlight">vendalo</span>.com</p>
    </div>
  </section>
</main>
</body>
</html>
```